SaaS / Consulting / Solution website redesign

We need a website design that:
- Is completely different than our current design : https://plumvessel.net
- Has a very minimal amount of copy
- Changes our positioning from a SaaS application to a solutions company. Solutions company means that we help our customers solve their problems with consulting, training, and tools. An example of a solutions company is here: https://oldpages.example/web/20130111103320/http://www.brindlework.com:80/
- Does not make us look like a start up
- Is more people oriented than technology oriented

We need a designer that:
- Is a rebel at heart
- Is a minimalist
- Tells us why our current site sucks
- Can disagree with us
- Can also do copywriting or already has a copywriter that can help
- Is ok with saying we have capability that we don't in order to see if people actually want that
- Can understand the difference between our grand vision and where we need to focus ourselves today in order to get there

Who we are:
- Entrepreneurs
- Programmers
- Consultants
- Investors

Here's our design goals:
#1 Get customers, investors, employers, and partners excited about our unique and clearly articulated value proposition
#2 Get people to contact us asking for help with their programs
#3 Position ourselves as an expert in the skills based volunteering, mentorship, and group collaboration
#4 Make it easy for people, who already know who we are, to register online

What our grand vision is:
- Create a marketplace where any person can go to our site and find time with anyone they need to meet with. Whether that is their hair stylist, school advisor, parent of your kids class, dentist, attorney, etc.

What will you get if you win:
- In addition to the prize of this project we will have many landing pages and other revisions we will need in the future. We currently don't have a designer or copywriter and need to add that capability to our team

Who do we need to appeal to:
- Directors that are launching innovative programs inside organizations
- IT personnel who are trying to disqualify our technology so they don't have to support it or deal with it when it doesn't go well
- Enterprise IT architects who don't want our product being on its own island within their organization totally incompatible with everything else. Architects which are trying to assess how our platform will co-exist with all their other platforms
- Vice Presidents who want to help their directors understand that we don't have enough experience to help them
- Program managers who have to juggle a million things and need a tool that actually helps instead of confuses them and adds more work for them.
- Program managers & directors that have been given ambiguous goals by their board of directors like "improve retention, increase engagement, create innovation, get people to collaborate." And who have no idea where to start or how to deliver on things like that.
- Program managers, directors, and vice presidents that are trying to understand how our technology and services fit into their existing technology and capability
- Employees who are bored and uninspired with their current tools and are hoping for some excitement in their life. Kind of like candy or a double espresso.
- Investors who think, our company like all the rest, are going to waste their money and make them look like a fool

Other information:
-The CSS and html needs to be responsive

-Our registration onboarding flow needs to collect this information:
User first name
user last name
user email
(verify their email)
user phone number
(verify their phone number)
User profile image (optional)
User profile summary (optional, like a bio, freeform text fiels)
If applicable: Register their organization
Organization name
Organization image (optional)
Account Mailing address
account Billing address (could be same as mailing address)
account Billing email address (could be same as user address)
account Product selection (pricing tier)
account Credit card information

The designs I am getting are a good start but they are only the front page. I just want you to know that I am expecting and need more than a landing page to complete the design. I will likely need a page that outlines the benefits and features of the product itself, how its different than our competitors, which will not be on the front page. I will need a registration flow. I will need a blog page design so we can post blog articles, I will need a team page, a page that goes into detail on our training, our services. I will likely need a page that shows all news and media we have been in. I need to show customer and user quotes, case studies, a way to contact us, partners, general resources like on collaboration, product tutorials, customers. I need the site to address a comprehensive set of needs. I need that design to be consistent and thorough. I know what PlateHarbor is. I'm not using because I need more than a template that was customized. I need to be unique and match our brand thoughtfully, beautifully, and artistically. Someone asked me a question about how Murmly is similar to our tool in the way it is referred by end users and purchased by managers. Our website needs to primarily talk to the managers as I explained in the brief but it needs to appear cool and exciting to our end-users without focusing on the technology too much. Murmly is a tool that teams use to collaborate in small and large enterprises. The value prop for them is that communication is easier. But they don't put that on their website. Why? Because the users of the technology won't go to the website to find out information on it, they get their information from someone who is using it and demos it to them. When Ines tells her manager Otto "Lets get murmly, Ruth is using it at her company and its great" Ines's manager doesn't know anything about murmly so she promptly googles it. The most important thing from Ines's perspective is that Otto agrees to try it out. Otto's biggest concern is that productivity will be enhanced to degraded. Murmly knows this and so on the front page they know they are talking to Otto NOT Ines because Ines is already sold on it and doesn't need to get sold on the website. Ines is end user. Otto is the purchaser. We have the same problem and so our end users are not the ones purchasing our product, their managers are purchasing our product. We get referred by our end users and vetted by their managers. Hope this helps! Thank you for looking at this project!  Added Wednesday, June 7, 2017

Another observation I am having about the designs being submitted. I believe we used the animations on our current website because animations / cartoons connect with the "inner child" in our users. Whatever that means :-). I think it's what makes our brand fun. I have a hard time imagining that we could make the design fun looking without animations but I'm sure it can be achieved. I also recognize that blending pictures of real people and animations is hard. So either we must masterfully blend them, use only animations, or make the real people have a LOT of fun! So far most of the designs while achieve the goal of appealing to the serious Vice Presidents and directors, they are not doing a good job at appealing to the overworked program managers and bored employees. There seems to stand another challenge with animations which is animations are hard to find and/or create that achieve the message / emotion we are trying to communicate. I don't have any good answers for this but I will say we can hire both animators and illustrators if we need to. All you have to do is communicate the effect in the website design with some simpler version maybe not the end illustration or animation itself. Added Wednesday, June 7, 2017

• Sex appeal and a sense of humor. Copy that makes people excited and clairvoyant about our potential.
• Boring renditions of other non-inspiring websites

```html
<!DOCTYPE html>
<html lang="en">
<head>
<meta charset="utf-8">
<title>Plumvessel — How engagement happens</title>
<link rel="stylesheet" href="https://fonts.googleapis.com/css2?family=Open+Sans:wght@400;600;700;800&display=swap">
<style>
:root{
  --blue:#1c9be8;
  --blue-dark:#1284cf;
  --ink:#2d3238;
  --muted:#7b838c;
  --line:#e3e6ea;
  --paper:#ffffff;
  --mist:#f3f5f7;
  --teal:#2f5d66;
  --green:#5aa83a;
  --green-deep:#3f8a2a;
}
*{box-sizing:border-box;margin:0;padding:0}
html,body{width:1200px;height:2920px;overflow:hidden}
body{font-family:"Open Sans",Arial,sans-serif;color:var(--ink);background:var(--paper);position:relative}
section,header,footer{position:absolute;left:0;width:1200px}
.btn{display:inline-block;font-size:12px;font-weight:700;letter-spacing:.5px;text-transform:uppercase;padding:13px 26px;border-radius:3px;background:var(--blue);color:#fff;border:2px solid var(--blue)}
.btn--ghost{background:transparent;color:var(--blue)}
.btn--light{background:transparent;border-color:#fff;color:#fff}
.btn--white{background:#fff;border-color:#fff;color:var(--green-deep)}

/* header */
.site-header{top:0;height:70px;background:#fff;display:flex;align-items:center;padding:0 60px;z-index:2}
.brand{display:flex;align-items:center;gap:8px;font-weight:700;font-size:20px;color:var(--green)}
.brand__dot{width:26px;height:26px;border-radius:50%;background:var(--green)}
.nav{margin-left:auto;display:flex;align-items:center;gap:26px;font-size:12px;color:var(--muted)}
.nav a{color:inherit;text-decoration:none}
.nav .is-active{color:var(--blue);font-weight:700}
.nav .btn{padding:7px 14px;font-size:11px}

/* hero */
.hero{top:70px;height:370px;background:linear-gradient(90deg,#fbfcfd 0%,#f1f3f5 100%)}
.hero__photo{position:absolute;right:0;top:0;width:580px;height:370px;background:linear-gradient(135deg,#e9ebee 0%,#c9cdd2 55%,#6d7278 100%)}
.hero__copy{position:absolute;left:100px;top:80px;width:500px}
.hero__title{font-size:32px;font-weight:800;color:var(--blue);letter-spacing:.5px;white-space:nowrap}
.hero__lead{margin-top:12px;font-size:16px;font-weight:700;line-height:1.45}
.hero .btn{position:absolute;left:100px;top:250px}

/* band */
.mission{top:440px;height:88px;background:var(--blue);color:#fff;text-align:center;padding-top:20px}
.mission__kicker{font-size:13px;opacity:.85}
.mission__line{font-size:22px;font-weight:600;margin-top:2px}

/* features */
.features{top:528px;height:552px;background:#fff}
.features__intro{position:absolute;left:140px;top:80px;width:350px}
.features__title{font-size:25px;font-weight:600;line-height:1.3}
.features__text{margin-top:14px;font-size:12px;line-height:1.7;color:var(--muted)}
.features__art{position:absolute;left:190px;top:300px;width:210px;height:210px;border-radius:50%;background:radial-gradient(circle,#e7b25a 0%,#d98c3a 45%,#3f8fb2 75%,#cfe4ef 100%)}
.feature-grid{position:absolute;left:560px;top:80px;width:490px;display:grid;grid-template-columns:1fr 1fr;gap:20px}
.feature-card{height:200px;background:#fff;border:1px solid var(--line);box-shadow:0 4px 14px rgba(0,0,0,.06);padding:26px 22px}
.feature-card--lead{background:var(--blue);border-color:var(--blue);color:#fff}
.feature-card__icon{width:34px;height:34px}
.feature-card__title{margin-top:14px;font-size:12px;font-weight:700;text-transform:uppercase;color:var(--blue)}
.feature-card--lead .feature-card__title{color:#fff}
.feature-card__text{margin-top:8px;font-size:11px;line-height:1.6;color:var(--muted)}
.feature-card--lead .feature-card__text{color:#dff0fc}

/* software */
.software{top:1080px;height:600px;background:var(--mist)}
.app-view{position:absolute;left:80px;top:80px;width:510px;height:440px;background:#fff;box-shadow:0 10px 30px rgba(0,0,0,.12);display:flex}
.app-view__side{width:110px;background:var(--teal);padding:18px 12px}
.app-view__brand{font-size:12px;font-weight:700;color:#fff;margin-bottom:22px}
.app-view__nav{height:8px;border-radius:4px;background:rgba(255,255,255,.35);margin-bottom:16px}
.app-view__main{flex:1;padding:20px;background:#f6f7f9}
.app-view__search{height:28px;background:#fff;border:1px solid var(--line);font-size:10px;color:var(--muted);padding:7px 10px}
.app-view__cols{display:grid;grid-template-columns:1fr 1fr;gap:14px;margin-top:18px}
.app-card{background:#fff;border:1px solid var(--line);padding:12px}
.app-card__head{font-size:10px;font-weight:700;color:var(--muted);margin-bottom:10px}
.person{display:flex;align-items:center;gap:8px;margin-bottom:10px;font-size:10px}
.person__avatar{width:24px;height:24px;border-radius:50%;background:#c79a82}
.software__copy{position:absolute;left:680px;top:150px;width:400px}
.software__title{font-size:28px;font-weight:600;line-height:1.3}
.software__text{margin-top:18px;font-size:12px;line-height:1.75;color:var(--muted)}

/* how it works */
.how{top:1680px;height:680px;background:linear-gradient(#eef1f4,#f7f8fa)}
.how__title{position:absolute;top:110px;width:100%;text-align:center;font-size:22px;font-weight:600}
.screen{position:absolute;background:#fff;box-shadow:0 8px 24px rgba(0,0,0,.12)}
.screen--side{top:190px;width:190px;height:370px;padding:14px}
.screen--left{left:330px}
.screen--right{left:680px}
.screen__bar{height:22px;background:var(--blue);margin:-14px -14px 12px}
.screen__row{font-size:9px;color:var(--muted);padding:7px 0;border-bottom:1px solid var(--line)}
.screen--main{left:440px;top:165px;width:320px;height:400px;z-index:1;padding:18px}
.picker__title{text-align:center;font-size:13px;font-weight:700;margin-bottom:10px}
.picker__date{background:var(--blue);color:#fff;font-size:11px;text-align:center;padding:6px;margin-bottom:12px}
.picker__tabs{display:grid;grid-template-columns:repeat(3,1fr);gap:6px;margin-bottom:12px}
.picker__tabs span{font-size:10px;text-align:center;padding:5px;border:1px solid var(--line)}
.picker__tabs .on{background:var(--blue);border-color:var(--blue);color:#fff}
.slots{display:grid;grid-template-columns:1fr 1fr;gap:6px}
.slots span{font-size:10px;text-align:center;padding:7px;border:1px solid var(--line);color:var(--muted)}
.picker__actions{display:grid;grid-template-columns:1fr 1fr;gap:6px;margin-top:14px}
.picker__actions span{font-size:10px;text-align:center;padding:8px;background:#cfd4d9;color:#fff}
.dots{position:absolute;top:628px;width:100%;display:flex;justify-content:center;gap:8px}
.dots i{width:8px;height:8px;border-radius:50%;background:#c9ced4}
.dots .on{background:var(--blue)}

/* team band */
.team{top:2360px;height:312px;background:linear-gradient(135deg,#7cc253 0%,#5aa83a 50%,#3f8a2a 100%);text-align:center;color:#fff}
.team__title{padding-top:90px;font-size:28px;font-weight:400;line-height:1.35}
.team__actions{margin-top:34px;display:flex;justify-content:center;gap:22px}

/* footer */
.site-footer{top:2672px;height:248px;background:#fff;padding:34px 140px 0}
.footer__about{width:420px}
.footer__about p{margin-top:12px;font-size:11px;line-height:1.6;color:var(--muted)}
.footer__ctas{margin-top:16px;display:flex;gap:12px}
.footer__ctas .btn{padding:8px 16px;font-size:10px}
.footer__cols{position:absolute;left:760px;top:40px;display:flex;gap:60px;font-size:10px;font-weight:700;color:var(--muted);text-transform:uppercase}
.subscribe{position:absolute;left:760px;top:80px;display:flex;gap:10px}
.subscribe__field{width:200px;height:28px;border-bottom:1px solid var(--line);font-size:10px;color:#aab0b6;padding-top:8px}
.subscribe .btn{padding:6px 14px;font-size:10px}
.social{position:absolute;left:960px;top:140px;display:flex;gap:14px}
.social i{width:14px;height:14px;border-radius:50%;background:#c9ced4}
.footer__legal{position:absolute;left:140px;right:140px;top:200px;border-top:1px solid var(--line);padding-top:14px;font-size:10px;color:var(--muted);display:flex;gap:40px}
.footer__legal span:first-child{margin-right:auto}
</style>
</head>
<body>

<header class="site-header">
  <div class="brand"><span class="brand__dot"></span>Plumvessel</div>
  <nav class="nav">
    <a class="is-active">Home</a><a>Product</a><a>About</a><a>Pricing</a><a>Features</a><a>Contact</a>
    <a class="btn btn--ghost">Register Now</a><a class="btn btn--ghost">Login</a>
  </nav>
</header>

<section class="hero">
  <div class="hero__photo" role="img" aria-label="Photo of a playful team posing in front of a grey wall"></div>
  <div class="hero__copy">
    <h1 class="hero__title">HOW ENGAGEMENT HAPPENS</h1>
    <p class="hero__lead">Plumvessel helps increase face-to-face engagement in your communities and groups with custom built solutions, training, consulting, and tools.</p>
  </div>
  <a class="btn">Request Demo</a>
</section>

<section class="mission">
  <p class="mission__kicker">Together we're going to change the world by</p>
  <p class="mission__line">connecting people in person</p>
</section>

<section class="features">
  <div class="features__intro">
    <h2 class="features__title">Increase face-to-face engagement in your communities and groups</h2>
    <p class="features__text">We help programs bring people together in real life. From mentoring to volunteering, our team and tools make every meeting simple, personal and worth the time.</p>
  </div>
  <div class="features__art" role="img" aria-label="Illustration of people gathered around a table seen from above"></div>
  <div class="feature-grid">
    <article class="feature-card feature-card--lead">
      <svg class="feature-card__icon" viewBox="0 0 34 34"><rect x="4" y="7" width="26" height="22" rx="2" fill="none" stroke="#fff" stroke-width="2"/><line x1="4" y1="13" x2="30" y2="13" stroke="#fff" stroke-width="2"/></svg>
      <h3 class="feature-card__title">Simplify face to face meetings</h3>
      <p class="feature-card__text">Find a shared time in seconds and meet people who matter.</p>
    </article>
    <article class="feature-card">
      <svg class="feature-card__icon" viewBox="0 0 34 34"><circle cx="12" cy="17" r="8" fill="none" stroke="#1c9be8" stroke-width="2"/><circle cx="22" cy="17" r="8" fill="none" stroke="#1c9be8" stroke-width="2"/></svg>
      <h3 class="feature-card__title">Seamless collaboration</h3>
      <p class="feature-card__text">Plan together across teams without long email threads.</p>
    </article>
    <article class="feature-card">
      <svg class="feature-card__icon" viewBox="0 0 34 34"><path d="M5 9h24v14H14l-6 5v-5H5z" fill="none" stroke="#1c9be8" stroke-width="2"/></svg>
      <h3 class="feature-card__title">Engaging interactions</h3>
      <p class="feature-card__text">Keep every conversation lively, useful and easy to follow.</p>
    </article>
    <article class="feature-card">
      <svg class="feature-card__icon" viewBox="0 0 34 34"><path d="M17 28C6 20 4 15 7 10c3-4 8-3 10 1 2-4 7-5 10-1 3 5 1 10-10 18z" fill="none" stroke="#1c9be8" stroke-width="2"/></svg>
      <h3 class="feature-card__title">Help people build relationships</h3>
      <p class="feature-card__text">Turn first meetings into lasting connections that grow.</p>
    </article>
  </div>
</section>

<section class="software">
  <div class="app-view">
    <div class="app-view__side">
      <div class="app-view__brand">Plumvessel</div>
      <div class="app-view__nav"></div><div class="app-view__nav"></div><div class="app-view__nav"></div><div class="app-view__nav"></div>
    </div>
    <div class="app-view__main">
      <div class="app-view__search">Meetings</div>
      <div class="app-view__cols">
        <div class="app-card">
          <div class="app-card__head">Mentors</div>
          <div class="person"><span class="person__avatar"></span>Ines Moreau</div>
          <div class="person"><span class="person__avatar"></span>Otto Brandt</div>
          <div class="person"><span class="person__avatar"></span>Ruth Kale</div>
        </div>
        <div class="app-card">
          <div class="app-card__head">Volunteers</div>
          <div class="person"><span class="person__avatar"></span>Lena Ward</div>
          <div class="person"><span class="person__avatar"></span>Tom Ruiz</div>
        </div>
        <div class="app-card">
          <div class="app-card__head">Groups</div>
          <div class="person"><span class="person__avatar"></span>Maya Fox</div>
        </div>
        <div class="app-card">
          <div class="app-card__head">Upcoming</div>
          <div class="person"><span class="person__avatar"></span>Noah Bell</div>
        </div>
      </div>
    </div>
  </div>
  <div class="software__copy">
    <h2 class="software__title">We're building software that connects people in person</h2>
    <p class="software__text">Programs live or die by the moments people spend together. Our platform handles the scheduling, reminders and follow-ups, so program managers can focus on the people instead of the paperwork. It fits into the tools your organization already uses, respects your IT standards, and scales from a single pilot group to an entire enterprise. Pair it with our consulting and training, and your mentoring, volunteering and collaboration programs get a clear plan, real momentum and results you can show your board.</p>
  </div>
</section>

<section class="how">
  <h2 class="how__title">Thats how Plumvessel works</h2>
  <div class="screen screen--side screen--left">
    <div class="screen__bar"></div>
    <div class="screen__row">Mon Jun 19, 2017</div><div class="screen__row">10:00am</div><div class="screen__row">11:30am</div><div class="screen__row">1:00pm</div><div class="screen__row">3:30pm</div>
  </div>
  <div class="screen screen--side screen--right">
    <div class="screen__bar"></div>
    <div class="screen__row">Tue Jun 20, 2017</div><div class="screen__row">9:00am</div><div class="screen__row">12:00pm</div><div class="screen__row">2:30pm</div><div class="screen__row">4:00pm</div>
  </div>
  <div class="screen screen--main">
    <div class="picker__title">Choose availability</div>
    <div class="picker__date">Mon Jun 19, 2017</div>
    <div class="picker__tabs"><span>30 min</span><span class="on">60 min</span><span>90 min</span></div>
    <div class="slots">
      <span>9:00am</span><span>9:30am</span><span>10:00am</span><span>10:30am</span><span>11:00am</span><span>1:00pm</span><span>1:30pm</span><span>2:00pm</span><span>3:00pm</span><span>4:00pm</span>
    </div>
    <div class="picker__actions"><span>Cancel</span><span>Confirm</span></div>
  </div>
  <div class="dots"><i class="on"></i><i></i><i></i></div>
</section>

<section class="team" role="img" aria-label="Green-toned photo of a team working together">
  <h2 class="team__title">Because it takes the perfect team<br>to bring great innovations to life</h2>
  <div class="team__actions">
    <a class="btn btn--white">Request Demo</a>
    <a class="btn btn--light">Schedule Consultation</a>
  </div>
</section>

<footer class="site-footer">
  <div class="footer__about">
    <div class="brand"><span class="brand__dot"></span>Plumvessel</div>
    <p>We help organizations bring people together face to face through consulting, training and tools built for mentoring, volunteering and group collaboration.</p>
    <div class="footer__ctas"><a class="btn">Request Demo</a><a class="btn btn--ghost">Register Now</a></div>
  </div>
  <div class="footer__cols"><span>Product</span><span>About</span><span>Contact</span></div>
  <div class="subscribe"><div class="subscribe__field">Your email address</div><a class="btn">Subscribe</a></div>
  <div class="social"><i></i><i></i><i></i></div>
  <div class="footer__legal"><span>© 2017 Plumvessel Inc. All rights reserved. Plumvessel is a registered name of Plumvessel Inc.</span><span>Blog</span><span>Press</span></div>
</footer>

</body>
</html>
```